Brightlane Rapid Rinse Web Design

We are looking for a web design that highlights our state of the art fully automated commercial vehicle washing equipment. Similar system to a car wash however this system is meant for the largest vehicles on our roadways. Transport trucks with or without a trailer, busses both highway and school, RV's from 5th wheel type to A Class. Cement trucks, dump trucks, vac trucks, fuel trucks etc. Pick ups with utility trailers...Refrigerator truck clean outs.
Brightlane Rapid Rinse will wash your vehicle quickly and with a minimal impact on the environment

Home page
About us
Why Brightlane
Services and pricing
Videos of wash system
Fleets
contact us

Target Market(s)

Commercial vehicle owners and operators as well as corporate fleets. Includes busses, municipal, school and highway.both school and

Industry/Entity Type

transportation

Coding

Coded - Design and coding required

Number of Pages Required

5+ page

Font styles to use
Sans Serif

Colors
0054AA
0677BA
7BADD7
CADEEF
E8F1F8

Requirements
Must have
• Welcome page,why us page which describes the financial and environmental benefits. payment processing page, contact us page, Services which is washing vehicles and greasing for commercial vehicles that want that service and grease
Nice to have
• pictures of both clean and dirty commercial vehicles ie. before and after

```html
<!DOCTYPE html>
<html lang="en">
<head>
<meta charset="utf-8">
<title>Brightlane Rapid Rinse</title>
<link rel="stylesheet" href="https://fonts.googleapis.com/css2?family=Poppins:ital,wght@0,400;0,500;0,600;0,700;0,800;1,700;1,800&display=swap">
<style>
  :root{
    --blue:#0054AA;
    --blue-mid:#0677BA;
    --blue-soft:#7BADD7;
    --blue-pale:#CADEEF;
    --blue-ice:#E8F1F8;
    --grey:#EDEDED;
    --ink:#333;
    --dark:#222;
    --white:#fff;
  }
  html,body{margin:0;padding:0;overflow:hidden;}
  body{font-family:"Poppins",sans-serif;color:var(--ink);background:var(--white);}
  .page{position:relative;width:1200px;height:5282px;overflow:hidden;background:var(--white);}
  .abs{position:absolute;}
  .backdrop{position:absolute;left:0;top:0;}
  .heading{font-family:"Poppins",sans-serif;font-weight:800;font-style:italic;text-transform:uppercase;margin:0;letter-spacing:.5px;}

  /* nav */
  .nav{position:absolute;left:0;top:0;width:1200px;height:103px;background:var(--blue);}
  .brand{position:absolute;left:74px;top:18px;color:var(--white);font-weight:600;line-height:1;text-transform:uppercase;}
  .brand .b1{font-size:38px;letter-spacing:.5px;display:block;}
  .brand .b2{font-size:21px;letter-spacing:6px;display:block;margin-top:6px;padding-left:14px;}
  .menu{position:absolute;left:396px;top:44px;display:flex;gap:27px;margin:0;padding:0;list-style:none;}
  .menu li{color:var(--white);font-size:12.5px;font-weight:700;font-style:italic;text-transform:uppercase;}
  .menu li.active{border-bottom:2px solid var(--white);padding-bottom:2px;}

  /* hero */
  .hero-text{position:absolute;left:0;top:268px;width:1200px;text-align:center;color:var(--white);}
  .hero-text .t1{font-size:76px;line-height:1;}
  .hero-text .t2{font-size:54px;line-height:1;margin-top:4px;}
  .hero-text p{font-size:21px;font-weight:600;line-height:29px;margin:18px auto 0;width:640px;}
  .hero-btns{position:absolute;top:510px;left:358px;display:flex;gap:17px;}
  .btn-ghost{border:2px solid var(--white);color:var(--white);font-size:13px;font-weight:700;text-transform:uppercase;padding:0 20px;height:44px;line-height:44px;}
  .dots{position:absolute;left:74px;top:692px;display:flex;gap:8px;}
  .dots span{width:10px;height:10px;background:var(--white);}
  .dots span:first-child{background:var(--blue-soft);}

  /* mission */
  .mission{position:absolute;left:74px;top:905px;width:1052px;text-align:center;color:var(--white);}
  .mission h2{font-size:40px;}
  .mission p{font-size:17.5px;line-height:33px;margin:14px auto 0;width:920px;}

  /* about */
  .about{position:absolute;left:615px;top:1497px;width:520px;}
  .about h2{color:var(--blue);font-size:38px;line-height:46px;}
  .about p{font-size:13.5px;line-height:24px;margin:24px 0 0;width:500px;}
  .btn-solid{display:inline-block;background:var(--blue-mid);color:var(--white);font-size:13.5px;font-weight:700;text-transform:uppercase;padding:0 32px;height:46px;line-height:46px;}
  .about .btn-solid{margin-top:20px;}

  /* services */
  .section-title{position:absolute;left:0;width:1200px;text-align:center;color:var(--blue);font-size:38px;}
  .svc{position:absolute;top:2165px;width:330px;height:340px;}
  .svc .label{position:absolute;left:0;bottom:22px;width:100%;text-align:center;color:var(--white);font-size:19px;}

  /* pricing */
  .price-card{position:absolute;top:2827px;width:511px;height:539px;background:var(--white);}
  .price-card .photo{height:240px;}
  .price-card h3{position:absolute;left:17px;top:270px;color:var(--blue-mid);font-size:24px;}
  .badge{position:absolute;left:398px;top:267px;width:88px;height:94px;background:var(--dark);border-radius:8px;color:var(--white);text-align:center;}
  .badge .amt{font-size:42px;font-weight:800;line-height:1;margin-top:14px;}
  .badge .amt sup{font-size:20px;vertical-align:top;position:relative;top:4px;}
  .badge .per{font-size:11px;font-weight:700;font-style:italic;}
  .ticks{position:absolute;left:17px;top:317px;margin:0;padding:0;list-style:none;}
  .ticks li{display:flex;align-items:center;gap:14px;font-size:13px;height:30.5px;}
  .price-card .btn-solid{position:absolute;left:17px;top:468px;padding:0 34px;}

  /* before after */
  .ba{position:absolute;top:3674px;height:364px;}
  .ba .tag{position:absolute;left:12px;bottom:10px;color:var(--white);font-size:16px;}
  .arrow{position:absolute;top:3826px;}

  /* contact */
  .contact h2{position:absolute;left:615px;top:4322px;color:var(--white);font-size:40px;}
  .field{position:absolute;background:var(--white);font-size:12.5px;color:#999;padding:0 14px;box-sizing:border-box;line-height:46px;height:47px;}
  .field.msg{line-height:normal;padding-top:14px;height:108px;}
  .submit{position:absolute;left:617px;top:4648px;width:151px;height:47px;line-height:47px;text-align:center;background:var(--blue-mid);color:var(--white);font-size:13.5px;font-weight:700;}

  /* footer */
  .foot-brand{position:absolute;left:74px;top:4993px;color:var(--blue);font-weight:600;text-transform:uppercase;line-height:1;}
  .foot-brand .b1{font-size:27px;display:block;}
  .foot-brand .b2{font-size:15px;letter-spacing:4px;display:block;margin-top:5px;padding-left:8px;}
  .foot-small{position:absolute;left:74px;top:5080px;font-size:11.5px;line-height:24px;color:var(--dark);}
  .social{position:absolute;left:74px;top:5146px;display:flex;gap:16px;}
  .social span{width:20px;height:20px;border-radius:50%;background:var(--blue);}
  .foot-col{position:absolute;top:4970px;}
  .foot-col h4{margin:0 0 10px;color:var(--blue);font-size:18px;}
  .foot-col ul{margin:0;padding:0;list-style:none;}
  .foot-col li{font-size:13px;line-height:27.7px;color:var(--dark);}
  .info{position:absolute;left:885px;display:flex;align-items:center;gap:14px;font-size:13px;line-height:26px;color:var(--dark);}
  .info .ic{width:40px;height:40px;border:1.5px solid var(--blue);border-radius:50%;display:flex;align-items:center;justify-content:center;flex:none;}
</style>
</head>
<body>
<div class="page">

  <svg class="backdrop" width="1200" height="5282" viewBox="0 0 1200 5282" aria-hidden="true">
    <defs>
      <linearGradient id="heroFill" x1="0" y1="0" x2="1" y2="1">
        <stop offset="0" stop-color="#0a2f6e"/><stop offset=".5" stop-color="#1a4d9c"/><stop offset="1" stop-color="#0b2a60"/>
      </linearGradient>
      <linearGradient id="missionFill" x1="0" y1="0" x2="1" y2="1">
        <stop offset="0" stop-color="#0b4fa3"/><stop offset=".5" stop-color="#2a6fc4"/><stop offset="1" stop-color="#0a4894"/>
      </linearGradient>
      <linearGradient id="darkFill" x1="0" y1="0" x2="1" y2="1">
        <stop offset="0" stop-color="#2d2d2d"/><stop offset=".5" stop-color="#3c3a38"/><stop offset="1" stop-color="#1f1f1f"/>
      </linearGradient>
    </defs>
    <!-- hero -->
    <polygon points="0,760 1200,655 1200,690 0,800" fill="var(--blue-soft)"/>
    <polygon points="0,0 1200,0 1200,650 0,770" fill="url(#heroFill)"/>
    <!-- mission -->
    <polygon points="74,872 1126,790 1126,1165 74,1245" fill="url(#missionFill)"/>
    <!-- grey about band -->
    <polygon points="0,1368 1200,1245 1200,1920 0,2040" fill="var(--grey)"/>
    <polygon points="74,1344 1126,1250 1126,1264 74,1358" fill="var(--blue-soft)"/>
    <polygon points="0,2026 1126,1916 1126,1930 0,2040" fill="var(--blue-soft)"/>
    <polygon points="90,1445 262,1480 90,1505" fill="var(--blue-soft)"/>
    <polygon points="586,1832 586,1892 412,1876" fill="var(--blue-soft)"/>
    <!-- pricing dark band -->
    <polygon points="0,2720 1200,2612 1200,3462 0,3560" fill="url(#darkFill)"/>
    <polygon points="74,2680 1200,2590 1200,2605 74,2696" fill="var(--blue-soft)"/>
    <polygon points="74,3556 1200,3452 1200,3466 74,3570" fill="var(--blue-soft)"/>
    <!-- contact blue band -->
    <polygon points="0,4210 1200,4100 1200,4828 0,4920" fill="var(--blue)"/>
    <polygon points="74,4178 1200,4086 1200,4100 74,4192" fill="var(--blue-soft)"/>
    <polygon points="90,4312 262,4348 90,4372" fill="var(--blue-soft)"/>
    <polygon points="586,4712 586,4775 412,4760" fill="var(--blue-soft)"/>
  </svg>

  <!-- hero photo area marker -->
  <div class="abs" role="img" aria-label="Truck entering the automated wash bay, blue toned" style="left:0;top:103px;width:1200px;height:560px;"></div>

  <header class="nav">
    <div class="brand"><span class="b1">Brightlane</span><span class="b2">Rapid Rinse</span></div>
    <ul class="menu">
      <li class="active">Home</li><li>About us</li><li>Why Brightlane</li><li>Services</li><li>Pricing</li><li>Videos</li><li>Fleets</li><li>Contact us</li>
    </ul>
  </header>

  <section class="hero-text">
    <div class="heading t1">Brightlane</div>
    <div class="heading t2">Rapid Rinse</div>
    <p>Temporibus autem quibusdam et aut officiis debitis aut rerum necessitatibus saepe eveniet ut et voluptates repudiandae sint.</p>
  </section>
  <div class="hero-btns">
    <span class="btn-ghost">Book a wash</span><span class="btn-ghost">Learn more</span><span class="btn-ghost">Contact us</span>
  </div>
  <div class="dots"><span></span><span></span><span></span><span></span></div>

  <section class="mission" role="img" aria-label="Mission panel over a photo of the wash brushes">
    <h2 class="heading">Our Mission</h2>
    <p>Sed ut perspiciatis unde omnis iste natus error sit voluptatem&nbsp; accusantium doloremque laudantium, totam rem aperiam, eaque ipsa quae ab illo inventore veritatis et quasi architecto beatae vitae dicta sunt explicabo. Nemo enim ipsam voluptatem quia voluptas sit aspernatur aut odit aut fugit, sed quia consequuntur magni dolores eos qui&nbsp; ratione voluptatem.</p>
  </section>

  <svg class="abs" style="left:74px;top:1462px" width="512" height="414" role="img" aria-label="Blue semi truck inside the wash bay">
    <defs><linearGradient id="aboutPhoto" x1="0" y1="0" x2="1" y2="1"><stop offset="0" stop-color="#4b7f86"/><stop offset=".5" stop-color="#2a5a9e"/><stop offset="1" stop-color="#6d7a82"/></linearGradient></defs>
    <polygon points="0,22 512,0 512,390 0,412" fill="url(#aboutPhoto)"/>
  </svg>

  <section class="about">
    <h2 class="heading">About Brightlane<br>Rapid Rinse</h2>
    <p>Sed ut perspiciatis unde omnis iste natus error sit voluptatem accusantium doloremque laudantium, totam rem aperiam, eaque ipsa quae ab illo inventore veritatis et quasi architecto beatae vitae dicta sunt explicabo. Nemo enim ipsam voluptatem quia voluptas sit aspernatur aut odit aut fugit, sed quia consequuntur magni dolores eos qui ratione voluptatem.</p>
    <span class="btn-solid">Read more</span>
  </section>

  <h2 class="heading section-title" style="top:2080px;">Our Services</h2>
  <div class="svc" style="left:74px;background:linear-gradient(180deg,#7a5a80 0%,#c0a0b8 35%,#8d98a4 65%,#0677BA 100%);" role="img" aria-label="Truck front passing through pink wash brushes"><span class="heading label">Automated Truck Wash</span></div>
  <div class="svc" style="left:435px;background:linear-gradient(180deg,#6b6660 0%,#4d4944 45%,#3f5a78 72%,#0677BA 100%);" role="img" aria-label="Mechanic greasing a heavy vehicle wheel"><span class="heading label">Additional Services</span></div>
  <div class="svc" style="left:797px;background:linear-gradient(180deg,#a9b8c8 0%,#e2e6ea 40%,#8fb0cf 70%,#0677BA 100%);" role="img" aria-label="Row of white fleet vans"><span class="heading label">Fleet Services</span></div>

  <h2 class="heading section-title" style="top:2742px;color:var(--white);">Pricing Packages</h2>

  <article class="price-card" style="left:74px;">
    <div class="photo" style="background:linear-gradient(135deg,#9a8f84,#d47a2c 45%,#8c9096);" role="img" aria-label="Worker washing an orange garbage truck"></div>
    <h3 class="heading">Individual Pricing</h3>
    <div class="badge"><div class="amt"><sup>$</sup>59</div><div class="per">Per Month</div></div>
    <ul class="ticks">
      <li><svg width="13" height="11" viewBox="0 0 13 11"><path d="M1 6l4 4 7-9" fill="none" stroke="#0677BA" stroke-width="2.4"/></svg>Sed ut perspiciatis unde omnis iste</li>
      <li><svg width="13" height="11" viewBox="0 0 13 11"><path d="M1 6l4 4 7-9" fill="none" stroke="#0677BA" stroke-width="2.4"/></svg>Natus error sit voluptatem</li>
      <li><svg width="13" height="11" viewBox="0 0 13 11"><path d="M1 6l4 4 7-9" fill="none" stroke="#0677BA" stroke-width="2.4"/></svg>Accusantium doloremque laudantium</li>
      <li><svg width="13" height="11" viewBox="0 0 13 11"><path d="M1 6l4 4 7-9" fill="none" stroke="#0677BA" stroke-width="2.4"/></svg>Totam rem aperiam, eaque ipsa quae ab illo inventore</li>
      <li><svg width="13" height="11" viewBox="0 0 13 11"><path d="M1 6l4 4 7-9" fill="none" stroke="#0677BA" stroke-width="2.4"/></svg>Veritatis et quasi architecto beatae</li>
    </ul>
    <span class="btn-solid">More info</span>
  </article>

  <article class="price-card" style="left:615px;">
    <div class="photo" style="background:linear-gradient(135deg,#2f5fa8,#e8ecf0 45%,#1f56a8 80%,#5a6470);" role="img" aria-label="Two white fleet vans parked outside a blue building"></div>
    <h3 class="heading">Fleet Packages</h3>
    <div class="badge"><div class="amt"><sup>$</sup>75</div><div class="per">Per Month</div></div>
    <ul class="ticks">
      <li><svg width="13" height="11" viewBox="0 0 13 11"><path d="M1 6l4 4 7-9" fill="none" stroke="#0677BA" stroke-width="2.4"/></svg>Sed ut perspiciatis unde omnis iste</li>
      <li><svg width="13" height="11" viewBox="0 0 13 11"><path d="M1 6l4 4 7-9" fill="none" stroke="#0677BA" stroke-width="2.4"/></svg>Natus error sit voluptatem</li>
      <li><svg width="13" height="11" viewBox="0 0 13 11"><path d="M1 6l4 4 7-9" fill="none" stroke="#0677BA" stroke-width="2.4"/></svg>Accusantium doloremque laudantium</li>
      <li><svg width="13" height="11" viewBox="0 0 13 11"><path d="M1 6l4 4 7-9" fill="none" stroke="#0677BA" stroke-width="2.4"/></svg>Totam rem aperiam, eaque ipsa quae ab illo inventore</li>
      <li><svg width="13" height="11" viewBox="0 0 13 11"><path d="M1 6l4 4 7-9" fill="none" stroke="#0677BA" stroke-width="2.4"/></svg>Veritatis et quasi architecto beatae</li>
    </ul>
    <span class="btn-solid">More info</span>
  </article>

  <h2 class="heading section-title" style="top:3598px;">Before &amp; After</h2>
  <div class="ba" style="left:0;width:267px;background:linear-gradient(135deg,#c9ccd0,#8a1f24 50%,#6b6f74);" role="img" aria-label="Clean red truck after washing"><span class="heading tag">After</span></div>
  <div class="ba" style="left:316px;width:283px;background:linear-gradient(160deg,#5e6a70,#a9a48c 50%,#7b7f78);" role="img" aria-label="Dirty bus before washing"><span class="heading tag">Before</span></div>
  <div class="ba" style="left:599px;width:285px;background:linear-gradient(160deg,#4f5c64,#c8ced4 50%,#6a7680);" role="img" aria-label="Clean bus after washing"><span class="heading tag">After</span></div>
  <div class="abs" style="left:597px;top:3674px;width:3px;height:364px;background:var(--white);"></div>
  <svg class="abs" style="left:580px;top:3838px" width="38" height="38" aria-hidden="true"><circle cx="19" cy="19" r="18" fill="#fff"/><path d="M16 13l-6 6 6 6M22 13l6 6-6 6" fill="none" stroke="#333" stroke-width="1.8"/></svg>
  <div class="ba" style="left:932px;width:268px;background:linear-gradient(150deg,#9c8f6a,#5a4a3a 50%,#3c3632);" role="img" aria-label="Muddy truck wheels before washing"><span class="heading tag">Before</span></div>
  <svg class="arrow" style="left:276px" width="28" height="60" aria-hidden="true"><path d="M22 6L6 30l16 24" fill="none" stroke="#222" stroke-width="3"/></svg>
  <svg class="arrow" style="left:894px" width="28" height="60" aria-hidden="true"><path d="M6 6l16 24L6 54" fill="none" stroke="#222" stroke-width="3"/></svg>

  <svg class="abs" style="left:74px;top:4334px" width="512" height="420" role="img" aria-label="White truck under red and black wash brushes">
    <defs><linearGradient id="contactPhoto" x1="0" y1="0" x2="1" y2="1"><stop offset="0" stop-color="#b8bcc2"/><stop offset=".5" stop-color="#8c2a34"/><stop offset="1" stop-color="#9ea4ac"/></linearGradient></defs>
    <polygon points="0,22 512,0 512,396 0,418" fill="url(#contactPhoto)"/>
  </svg>

  <section class="contact">
    <h2 class="heading">Contact Us</h2>
    <div class="field" style="left:615px;top:4405px;width:248px;">First Name</div>
    <div class="field" style="left:878px;top:4405px;width:248px;">Last Name</div>
    <div class="field" style="left:615px;top:4465px;width:248px;">Email Address</div>
    <div class="field" style="left:878px;top:4465px;width:248px;">Phone No</div>
    <div class="field msg" style="left:615px;top:4523px;width:511px;">Message</div>
    <div class="submit">SUBMIT</div>
  </section>

  <footer>
    <div class="foot-brand"><span class="b1">Brightlane</span><span class="b2">Rapid Rinse</span></div>
    <div class="foot-small">© 2024 Brightlane Rapid Rinse<br>All Rights Reserved. Privacy policy</div>
    <div class="social"><span></span><span></span><span></span><span></span><span></span></div>

    <div class="foot-col" style="left:411px;">
      <h4 class="heading">Quick Links</h4>
      <ul><li>Home</li><li>About us</li><li>Why Brightlane</li><li>Services</li><li>Pricing</li><li>Videos of Wash System</li><li>Fleets</li><li>Contact us</li></ul>
    </div>
    <div class="foot-col" style="left:665px;">
      <h4 class="heading">Services</h4>
      <ul><li>Automated Truck Wash</li><li>Additional Services</li><li>Fleet Services</li></ul>
    </div>
    <div class="foot-col" style="left:885px;">
      <h4 class="heading">Contact Info</h4>
    </div>
    <div class="info" style="top:5015px;">
      <span class="ic"><svg width="16" height="16" viewBox="0 0 16 16"><path d="M8 1a5 5 0 0 0-5 5c0 4 5 9 5 9s5-5 5-9a5 5 0 0 0-5-5zm0 7a2 2 0 1 1 0-4 2 2 0 0 1 0 4z" fill="#0054AA"/></svg></span>
      <span>48 Harbour Lane, Unit 12,<br>Riverton 20417, United States</span>
    </div>
    <div class="info" style="top:5094px;">
      <span class="ic"><svg width="16" height="16" viewBox="0 0 16 16"><path d="M4 1l3 3-2 2a9 9 0 0 0 5 5l2-2 3 3-2 3C7 15 1 9 1 3z" fill="#0054AA"/></svg></span>
      <span>+1-555-014-2290</span>
    </div>
    <div class="info" style="top:5152px;">
      <span class="ic"><svg width="16" height="12" viewBox="0 0 16 12"><rect x="0" y="0" width="16" height="12" rx="1" fill="#0054AA"/><path d="M1 1l7 6 7-6" fill="none" stroke="#fff" stroke-width="1.4"/></svg></span>
      <span>hello@brightlanerinse.com</span>
    </div>
  </footer>
</div>
</body>
</html>
```